We need a business card for our gym. We are a PowerCore affiliate in Decatur Georgie established 2008. Our company name is Rally Functional Fitness. PowerCore Building Prime Fitness. Instagram and website is @rallygym. Hashtags we use #rallywithheart #madetorally We want something similar to the the black and neon green design attached but a different color scheme. No neon colors. Are company colors are the same as the blue and white card attached. We are open to ideas as far as colors however - just no neon.

Contact Information for Business Card

Rally Functional Fitness
472 Halvern Drive
Decatur GA 30041
Phone 404.555.0187 Website www.rallygym.example

Font styles to use
Other font styles liked:
• Futura Extra Bold Condensed

Colors

Designer to choose colors to be used in the design.

Requirements
Must have
• Our primary font we typically use for our name is Futura Extra Bold Condensed
Nice to have
• I attached a card from that is black and neon green from Zorva that we would like something similar. The blue and white is more similar to our colors. We also use have used black and white in the past. We use the chevrons as out logo. We are a PowerCore affiliate so I included a logo from them as well that may or may not be used on the card. Our instagram is @rallygym hashtags #madetorally #rallywithheart
Should not have
• No neon colors

```html
<!DOCTYPE html>
<html lang="en">
<head>
<meta charset="utf-8">
<title>Rally Functional Fitness – Business Card</title>
<link rel="stylesheet" href="https://fonts.googleapis.com/css2?family=Lato:wght@400;700;900&display=swap">
<style>
  :root {
    --stage: #2b2b2d;
    --card: #0e0e0f;
    --facet-1: #161617;
    --facet-2: #1b1b1c;
    --facet-3: #121213;
    --brand-blue: #1d5cf5;
    --text-white: #e9e9ec;
    --hairline: #3a3a3e;
  }
  * { box-sizing: border-box; margin: 0; padding: 0; }
  html, body {
    width: 1200px; height: 866px; overflow: hidden;
    background: var(--stage);
    font-family: "Lato", Arial, sans-serif;
  }
  .card {
    position: absolute; left: 75px; top: 133px;
    width: 1050px; height: 600px;
    background: var(--card);
    overflow: hidden;
    box-shadow: 0 18px 40px rgba(0,0,0,.45);
  }
  .card__facets { position: absolute; inset: 0; width: 100%; height: 100%; }
  .card__band {
    position: absolute; left: 0; right: 0; bottom: 0; height: 16px;
    background: var(--brand-blue);
  }
  .contact { position: absolute; left: 62px; top: 118px; color: var(--text-white); }
  .contact__name {
    font-weight: 900; font-size: 36px; letter-spacing: .5px;
    color: var(--brand-blue); text-transform: uppercase; line-height: 1;
  }
  .contact__role { font-size: 26px; margin-top: 6px; }
  .contact__list { list-style: none; margin-top: 12px; font-size: 24px; line-height: 34px; }
  .contact__list li { display: flex; align-items: center; gap: 12px; }
  .contact__icon { width: 20px; height: 20px; flex: none; }
  .brand {
    position: absolute; left: 440px; top: 232px;
    display: flex; align-items: center; gap: 16px;
  }
  .brand__mark { width: 20px; height: 20px; background: var(--brand-blue); flex: none; }
  .brand__name {
    color: var(--brand-blue); font-weight: 900; font-size: 40px; line-height: 1;
    white-space: nowrap;
  }
  .card__rule {
    position: absolute; left: 420px; right: 62px; top: 385px;
    height: 1px; background: var(--hairline);
  }
  .address {
    position: absolute; right: 62px; bottom: 58px;
    text-align: right; color: var(--text-white); font-size: 28px; line-height: 1.2;
    font-style: normal;
  }
  .address__company {
    color: var(--brand-blue); font-weight: 900; font-size: 26px;
    text-transform: uppercase; margin-bottom: 4px;
  }
</style>
</head>
<body>
  <article class="card">
    <svg class="card__facets" viewBox="0 0 1050 600" aria-hidden="true">
      <polygon points="230,0 520,0 760,600 470,600" fill="var(--facet-1)"/>
      <polygon points="330,0 430,0 560,420 470,600" fill="var(--facet-2)"/>
      <polygon points="520,0 780,0 1050,330 1050,600 760,600" fill="var(--facet-3)"/>
      <polygon points="0,280 230,0 330,0 120,600 0,600" fill="var(--facet-3)"/>
    </svg>

    <section class="contact">
      <h1 class="contact__name">Daniel Brooks</h1>
      <p class="contact__role">Managing Director</p>
      <ul class="contact__list">
        <li>
          <svg class="contact__icon" viewBox="0 0 20 20" aria-hidden="true"><path d="M4 2h4l1.5 4-2 1.5a10 10 0 0 0 5 5L14 10.5l4 1.5v4a2 2 0 0 1-2 2A14 14 0 0 1 2 4a2 2 0 0 1 2-2z" fill="var(--brand-blue)"/></svg>
          404.555.0187
        </li>
        <li>
          <svg class="contact__icon" viewBox="0 0 20 20" aria-hidden="true"><circle cx="10" cy="10" r="8" fill="none" stroke="var(--brand-blue)" stroke-width="2.4"/><path d="M2 10h16M10 2c3 3 3 13 0 16M10 2c-3 3-3 13 0 16" fill="none" stroke="var(--brand-blue)" stroke-width="1.6"/></svg>
          www.rallygym.example
        </li>
        <li>
          <svg class="contact__icon" viewBox="0 0 20 20" aria-hidden="true"><rect x="2" y="2" width="16" height="16" fill="var(--brand-blue)"/></svg>
          @rallygym
        </li>
      </ul>
    </section>

    <div class="brand">
      <span class="brand__mark" aria-hidden="true"></span>
      <p class="brand__name">Rally Functional Fitness</p>
    </div>

    <div class="card__rule" aria-hidden="true"></div>

    <address class="address">
      <p class="address__company">Rally Functional Fitness</p>
      <p>472 Halvern Drive</p>
      <p>Decatur GA 30041</p>
    </address>

    <div class="card__band" aria-hidden="true"></div>
  </article>
</body>
</html>
```